Natural healthcare clinic needs stationery and business card design

We have had a logo developed by Pixel Harbor and are now looking at utilising it for a new business concept. The concept is a natural healthcare clinic that hosts a number of small businesses. The individual practitioners may want to utilise the host business stationery to provide a consistent message to clients.

I am looking for a stationery design - letterhead, DL brochure template and business card that uses our logo. The business name 'Bright Meadows' is all about getting rhythm back into your life so you can be fit and healthy. The stationery design should reflect this.

There are a couple of requirements for the business card, it needs to be double-sided with black and white back. There should be lines to write appointment times on. The cards may need to be custom named on the front for example Carol Fenwick, Remedial Therapist and Aromatherapist. Therefore if a template can be provided so we can customise this information using MS Publisher, it would be appreciated.

The DL brochure template needs to be A4 folded to DL. I am looking for a consistent brand message that can be utilised to produce our own clinic brochures.

The natural healthcare clinic will host the following types of businesses - remedial massage, pregnancy massage, oncology massage, aromatherapy, acupuncture - as a bit of a guide.

Target Market(s)

25-45 year old male and females who work full time.

Industry/Entity Type

Healthcare

Requirements
Must have
• Use the logo I have already.

```html
<!DOCTYPE html>
<html lang="en">
<head>
<meta charset="utf-8">
<title>Bright Meadows — Stationery Set</title>
<link rel="stylesheet" href="https://fonts.googleapis.com/css2?family=Questrial&family=PT+Sans:wght@400;700&display=swap">
<style>
  :root{
    --backdrop:#e8e5e0;
    --paper:#ffffff;
    --paper-shade:#eeeeee;
    --charcoal:#2e2e30;
    --charcoal-deep:#232325;
    --flap:#5d5d5f;
    --leaf-green:#86b43c;
    --olive:#6c6a46;
    --ink:#2b2b2b;
    --rule:#8a8a8a;
    --brand-font:"Questrial", sans-serif;
    --body-font:"PT Sans", sans-serif;
  }
  *{box-sizing:border-box;margin:0;padding:0}
  html,body{width:1200px;height:811px;overflow:hidden}
  body{background:var(--backdrop);position:relative;font-family:var(--body-font);color:var(--ink)}
  .sheet{position:absolute;background:var(--paper);box-shadow:0 2px 6px rgba(0,0,0,.18)}

  .brand{font-family:var(--brand-font);color:var(--leaf-green);font-weight:400;white-space:nowrap;display:flex;align-items:center;gap:.3em}
  .brand-dot{display:inline-block;width:.55em;height:.55em;border-radius:50%;background:var(--leaf-green)}

  .band{position:absolute;bottom:0;height:10px;display:flex}
  .band-green{background:var(--leaf-green)}
  .band-olive{background:var(--olive)}
  .band-gap{background:var(--paper);width:2px}

  /* Letterhead */
  .letterhead{left:272px;top:103px;width:306px;height:417px}
  .letterhead .masthead{position:absolute;top:33px;left:0;right:0;height:20px}
  .letterhead .masthead-rule{position:absolute;top:16px;height:2px;background:var(--rule)}
  .letterhead .masthead .brand{position:absolute;left:50%;top:5px;transform:translateX(-50%);font-size:11px}
  .letter-body{position:absolute;left:26px;top:100px;width:262px;font-size:5.4px;line-height:7px}
  .letter-body p{margin-bottom:6px}
  .letter-body .gap{margin-bottom:16px}
  .letter-footer{position:absolute;left:0;right:0;bottom:14px;text-align:center;font-size:4.4px;color:#555}

  /* Presentation folder */
  .folder{left:610px;top:78px;width:355px;height:452px;background:radial-gradient(ellipse at 45% 55%,#3a3a3d 0%,var(--charcoal) 45%,var(--charcoal-deep) 100%)}
  .folder .brand{position:absolute;left:72px;top:258px;font-size:29px;color:var(--leaf-green)}

  /* Business cards */
  .card-back{left:120px;top:613px;width:70px;height:115px;background:var(--charcoal)}
  .card-back .brand{position:absolute;left:8px;top:68px;font-size:7px}
  .card-front{left:225px;top:614px;width:71px;height:113px}
  .card-front .brand{position:absolute;left:14px;top:22px;font-size:5.5px}
  .appointment{position:absolute;left:10px;top:47px;width:52px;font-size:3.6px;color:#555}
  .appointment div{display:flex;gap:2px;margin-bottom:7px;align-items:flex-end}
  .appointment span.line{flex:1;border-bottom:.5px dotted #999}
  .practitioner{position:absolute;left:10px;top:73px;width:56px;font-size:3.6px;line-height:4.6px;color:#444}
  .practitioner .name{color:var(--leaf-green);font-size:4.2px;font-weight:700}
  .practitioner .services{color:var(--leaf-green);margin-top:2px}
  .practitioner .contact{color:var(--leaf-green);margin-top:2px}

  /* DL compliments slip */
  .dl-slip{left:329px;top:562px;width:338px;height:168px;background:linear-gradient(180deg,#fff 0%,#f6f6f6 100%)}
  .dl-slip .brand{position:absolute;right:12px;top:38px;font-size:10px}

  /* DL envelope */
  .envelope{left:692px;top:562px;width:336px;height:165px}
  .envelope .flap{position:absolute;left:0;top:0;width:100%;height:52px;background:linear-gradient(180deg,#6a6a6c,var(--flap))}
  .envelope .brand{position:absolute;left:50%;top:31px;transform:translateX(-50%);font-size:8.5px}
</style>
</head>
<body>

  <!-- Letterhead -->
  <section class="sheet letterhead" aria-label="Letterhead">
    <header class="masthead">
      <div class="masthead-rule" style="left:0;width:93px"></div>
      <div class="masthead-rule" style="left:198px;width:108px"></div>
      <div class="brand"><span class="brand-dot"></span>Bright Meadows</div>
    </header>
    <div class="letter-body">
      <p>1420, Fernbrook Avenue<br>Pasadena, CA 91101.</p>
      <p>January 29th, 2011</p>
      <p>Mr. Ashworth<br>President, Ashworth Family Care Centre<br>58 Linden Row<br>Albany, NY 12207</p>
      <p>Dear Mr. Ashworth:</p>
      <p class="gap">In the first paragraph, one needs to give a brief introduction of oneself. One should also give reference to the purpose of the letter in brief.<br>The second paragraph needs to give the details of the letter and its need. This paragraph is mostly longer than the others and plays the main role in the letter. Keep the sentences short and to the point. Avoid using complex words and sentences.</p>
      <p>The third and last paragraph is the conclusion of the letter and can be kept short.</p>
      <p>Sincerely,</p>
      <p>(this is where the signature of the writer will be placed)</p>
      <p>Dana Whitlow<br>Read more at Letter Guide: http://www.letterguide.example/format-sample</p>
    </div>
    <div class="letter-footer">Website - www.brightmeadows.com.au &nbsp;·&nbsp; Email - hello@brightmeadows.com.au &nbsp;·&nbsp; Phone - 02 5550 1384</div>
    <div class="band" style="left:0;right:0">
      <div class="band-green" style="width:206px"></div><div class="band-gap"></div><div class="band-olive" style="flex:1"></div>
    </div>
  </section>

  <!-- Presentation folder -->
  <section class="sheet folder" aria-label="Presentation folder cover">
    <div class="brand"><span class="brand-dot"></span>Bright Meadows</div>
  </section>

  <!-- Business card back -->
  <section class="sheet card-back" aria-label="Business card back">
    <div class="brand"><span class="brand-dot"></span>Bright Meadows</div>
  </section>

  <!-- Business card front -->
  <section class="sheet card-front" aria-label="Business card front">
    <div class="brand"><span class="brand-dot"></span>Bright Meadows</div>
    <div class="appointment">
      <div>Date <span class="line"></span></div>
      <div>Time <span class="line"></span></div>
    </div>
    <div class="practitioner">
      <div class="name">Carol Fenwick</div>
      <div>Remedial Therapist &amp; Aromatherapist</div>
      <div class="services">Remedial massage, pregnancy massage, oncology massage, aromatherapy</div>
      <div class="contact">Mobile: 0400 555 218<br>carol@brightmeadows.com.au</div>
    </div>
  </section>

  <!-- DL compliments slip -->
  <section class="sheet dl-slip" aria-label="DL compliments slip">
    <div class="brand"><span class="brand-dot"></span>Bright Meadows</div>
    <div class="band" style="left:0;right:0">
      <div class="band-green" style="width:226px"></div><div class="band-gap"></div><div class="band-olive" style="flex:1"></div>
    </div>
  </section>

  <!-- DL envelope -->
  <section class="sheet envelope" aria-label="DL envelope">
    <div class="flap"></div>
    <div class="brand"><span class="brand-dot"></span>Bright Meadows</div>
    <div class="band" style="left:0;right:0;height:9px">
      <div class="band-green" style="width:227px"></div><div class="band-gap"></div><div class="band-olive" style="flex:1"></div>
    </div>
  </section>

</body>
</html>
```